Tiskoro

We need a business card for our company is a holding for different business all are different we try to have some air of relax and fun in our projects we add pictures of the office to give you an idea od the mood of the business

Business

```html
<!DOCTYPE html>
<html lang="en">
<head>
<meta charset="utf-8">
<title>Tiskoro — Business Card</title>
<link rel="stylesheet" href="https://fonts.googleapis.com/css2?family=Exo+2:wght@400;600;700&display=swap">
<style>
  :root {
    --canvas-bg: #e9e6e1;
    --card-white: #ffffff;
    --card-shade: #e6e6e6;
    --brand-yellow: #f5e92a;
    --brand-brown: #5e4029;
    --ink-dark: #2b2b2b;
    --ink-mid: #555555;
    --accent-blue: #3f8fd6;
  }
  * { box-sizing: border-box; margin: 0; padding: 0; }
  html, body { width: 1057px; height: 1200px; overflow: hidden; }
  body {
    background: var(--canvas-bg);
    font-family: "Exo 2", Arial, sans-serif;
    position: relative;
  }
  .card {
    position: absolute;
    top: 230px;
    width: 420px;
    height: 720px;
    background: linear-gradient(160deg, var(--card-white) 45%, var(--card-shade) 100%);
    box-shadow: 0 6px 24px rgba(0,0,0,0.18);
    overflow: hidden;
  }
  .card--front { left: 84px; }
  .card--back { left: 553px; }

  .brand {
    display: flex;
    align-items: center;
    gap: 12px;
    color: var(--brand-brown);
    font-weight: 700;
    font-size: 40px;
    letter-spacing: 0.5px;
  }
  .brand__square {
    width: 30px; height: 30px;
    background: var(--brand-yellow);
  }

  /* front */
  .front__band {
    position: absolute; top: 0; right: 0;
    width: 34px; height: 100%;
    background: var(--brand-brown);
  }
  .front__brand { position: absolute; top: 70px; right: 110px; }
  .front__details {
    position: absolute; right: 34px; top: 220px;
    width: 340px;
    text-align: right;
  }
  .person__name {
    font-size: 27px; font-weight: 600;
    letter-spacing: 2px; color: var(--ink-dark);
    padding-right: 74px;
  }
  .person__role {
    font-size: 11px; letter-spacing: 1.5px;
    text-transform: uppercase; color: var(--ink-mid);
    padding-right: 74px; margin-top: 2px;
  }
  .contact { list-style: none; margin-top: 34px; }
  .contact__item {
    display: flex; justify-content: flex-end; align-items: center;
    font-size: 15px; color: var(--ink-mid);
    height: 24px;
  }
  .contact__item::after {
    content: ""; display: block;
    width: 64px; height: 2px; margin-left: 10px;
    background: var(--brand-brown);
  }
  .contact__gap { height: 34px; }

  /* back */
  .back__brand {
    position: absolute; top: 300px; left: 50%;
    transform: translateX(-50%);
  }
  .back__web {
    position: absolute; left: 26px; bottom: 80px;
    width: 300px;
    border-top: 1.5px solid var(--accent-blue);
    border-bottom: 1.5px solid var(--accent-blue);
    padding: 12px 0;
    display: flex; align-items: center; gap: 14px;
    font-size: 15px; color: var(--ink-mid);
  }
  .back__web-icon {
    width: 18px; height: 18px;
    background: var(--brand-yellow);
  }
</style>
</head>
<body>
  <section class="card card--front" aria-label="Card front">
    <div class="front__brand brand">
      <span class="brand__square"></span><span>Tiskoro</span>
    </div>
    <div class="front__details">
      <h1 class="person__name">MARCO DELVANI</h1>
      <p class="person__role">General Manager</p>
      <ul class="contact">
        <li class="contact__item">42 Harbor Lane</li>
        <li class="contact__item">5th floor, East Wing</li>
        <li class="contact__gap"></li>
        <li class="contact__item">014 782 3390</li>
        <li class="contact__item">014 782 3391</li>
        <li class="contact__item">hello@tiskoro.co</li>
        <li class="contact__item">www.tiskoro-group.com</li>
      </ul>
    </div>
    <div class="front__band"></div>
  </section>

  <section class="card card--back" aria-label="Card back">
    <div class="back__brand brand">
      <span class="brand__square"></span><span>Tiskoro</span>
    </div>
    <div class="back__web">
      <span class="back__web-icon"></span>
      <span>www.tiskoro-group.com</span>
    </div>
  </section>
</body>
</html>
```